Basic Commercial & Residential Real Estate Web Site

I need a basic website for a new real estate company that deals with both residential and commercial sales. It must be clean and professional. We sell homes, office buildings, farms, and ranches. It should feel crisp and clean.
I need a main page with my logo and links to commercial, residential, farm and land searches with contact data forms. Also incorporated would be a mls property search (IDX) form. I am in Northern California and the current site I posted is at www.tlvarden.com. I need the functionality of the links and the supporting pages. I do not have all the copy ready because I did not know what to expect.
Updates

Project Deadline Extended
Reason: I apologize, I am extremely busy and you all need more data to do a good job. All the designs are great so far and it is extremely difficult to choose at this point. I haven't given you enough data. I haver now uploaded some relevent photos (not very good) and edited the brief. I am looking for what I call the Landing or main page with some functionality built in to other pages which I also need. Example if you click on "Commercial" it should go to a page that discusses our commercial dept.......

I would like to thank all the designers for all their hard work and efforts, I wish I could reward you all.

Thanks again for your creative and professional designs.

Edwin

Target Market(s)

Corporate Execs for the Commercial Buildings
Homeowners/Families for the Homes and Farms
Upper end people for the land to build estates

Industry/Entity Type

Real Estate

Font styles to use
Sans Serif

Requirements
Must have
• Our Logo should be prominent, pronounced
Need contact data or button
Functional Page that links to other data pages
Must Have a "search for properties" feature
Must say "Commercial and Residential Representation"
Pictures of Commercial Building and Nice Home (Tradtional not contemporary)
Nice to have
• Individual Buttons or links to "Commercial, Residential, Farm/Ranch, Land"
Contact Data displayed
button that says "Maple Crest"-next to button is Maple Crest Logo-see www.maplecrest.bz
Links to "Buyers and "Sellers"
Links to Facebook, twitter,.....etc
Should not have
• 20+ story commercial buildings or ultra modern. See uploaded files of typical buildings for commercial.

```html
<!DOCTYPE html>
<html lang="en">
<head>
<meta charset="utf-8">
<title>Properties by Varden</title>
<link rel="stylesheet" href="https://fonts.googleapis.com/css2?family=Open+Sans:wght@300;400;600&family=Ubuntu+Condensed&family=Noto+Serif&display=swap">
<style>
:root{
  --header:#2d2d2d;
  --footer:#2b2b2b;
  --bottom:#1f1f1f;
  --page:#f3f3f3;
  --white:#ffffff;
  --text:#222222;
  --blue:#1a93d3;
  --blue-box:#2a8ec8;
  --olive:#6d8a12;
  --olive-light:#8ea033;
  --card-band:rgba(20,20,20,.78);
  --rule:#67b9e4;
  --search-band:rgba(25,25,25,.72);
}
*{margin:0;padding:0;box-sizing:border-box}
html,body{width:693px;height:1200px;overflow:hidden}
body{position:relative;background:var(--page);font-family:"Open Sans",Arial,sans-serif;color:var(--text)}
.abs{position:absolute}

/* header */
.site-header{left:0;top:0;width:693px;height:73px;background:var(--header)}
.brand{left:59px;top:10px;color:var(--white);font-weight:300;line-height:1}
.brand-small{font-size:10px;letter-spacing:1px;margin-left:40px;display:block}
.brand-name{font-size:34px;letter-spacing:2px;display:block;margin-top:3px}
.user-links{right:57px;top:19px;font-size:7px;color:var(--olive-light)}
.user-links span{margin:0 3px;color:#777}
.main-nav{right:57px;top:44px;height:29px;display:flex;font-size:9.4px;color:var(--white)}
.main-nav a{color:inherit;text-decoration:none;padding:0 6.5px;line-height:29px;display:block}
.main-nav a.current{background:var(--white);color:var(--text);padding:0 10px}

/* hero */
.hero{left:0;top:73px;width:693px;height:307px;background:linear-gradient(180deg,#c7d6de 0%,#e3e6e2 35%,#bdb8b2 62%,#5d5c5e 78%,#3f4045 100%)}
.hero-caption{left:105px;top:156px;width:246px;height:128px;background:rgba(255,255,255,.28)}
.hero-kicker{left:124px;top:173px;font-size:21px;font-weight:300;color:var(--olive)}
.hero-title{left:124px;top:190px;font-size:66px;font-weight:300;color:#151515;line-height:1}
.slide-arrow{width:18px;height:18px;background:#111;color:#fff;font-size:9px;line-height:18px;text-align:center}

/* property search */
.property-search{left:59px;top:342px;width:577px;height:28px;background:var(--search-band);display:flex;align-items:center;padding:0 8px;gap:6px}
.tagline{color:var(--white);font-size:8.6px;font-weight:600;letter-spacing:.3px;flex:1;white-space:nowrap}
.search-field{height:17px;background:var(--white);color:#777;font-size:7px;line-height:17px;padding:0 6px;border:1px solid #ccc}
.search-field.type{width:88px}
.search-field.place{width:92px}
.search-button{height:17px;background:var(--blue-box);color:var(--white);font-size:7px;font-weight:600;line-height:17px;padding:0 9px;white-space:nowrap}

/* property cards */
.card{top:404px;width:167px;height:210px;background:var(--white);box-shadow:0 1px 3px rgba(0,0,0,.25)}
.card-photo{position:absolute;left:0;top:0;width:167px;height:135px}
.card-label{position:absolute;left:0;top:114px;width:167px;height:21px;background:var(--card-band);color:var(--blue);font-size:11px;line-height:21px;padding-left:10px;font-family:"Ubuntu Condensed","Open Sans",sans-serif;text-transform:uppercase;letter-spacing:.3px}
.card-text{position:absolute;left:10px;top:149px;width:150px;font-size:7.2px;line-height:9.5px;color:var(--text)}
.read-more{font-size:7.4px;color:var(--olive)}
.card .read-more{position:absolute;right:10px;top:190px}

/* sections */
.section-head{display:flex;align-items:flex-end;gap:6px;width:374px}
.section-title{font-family:"Ubuntu Condensed","Open Sans",sans-serif;font-weight:400;font-size:17px;line-height:18px;color:var(--blue);white-space:nowrap}
.section-rule{flex:1;height:1px;background:var(--rule);margin-bottom:4px}
.feature-photo{width:143px;height:93px}
.feature-text{width:215px;font-size:7.3px;line-height:12.2px;color:#111}

/* discussions */
.discussions{left:469px;top:641px;width:167px;height:303px;background:#f7f7f7;box-shadow:0 1px 3px rgba(0,0,0,.25)}
.discussions-head{position:absolute;left:7px;top:6px;width:154px;height:33px;background:#f1f1f1;box-shadow:0 1px 2px rgba(0,0,0,.25);font-family:"Noto Serif",Georgia,serif;font-size:8.4px;line-height:33px;padding-left:16px;color:#222}
.post{position:absolute;left:7px;width:154px;height:32px;background:var(--white);box-shadow:0 1px 2px rgba(0,0,0,.22);font-size:7.2px;color:#111}
.post:nth-of-type(even){background:#f1f1f1}
.post svg{position:absolute;left:6px;top:6px}
.post-title{position:absolute;left:26px;top:4px}
.post-meta{position:absolute;left:26px;top:17px;width:122px}
.post-meta b{font-weight:400;color:var(--olive-light)}
.post-meta .date{position:absolute;right:6px;top:0}
.view-all{position:absolute;left:34px;top:284px;width:102px;height:19px;background:#3a3a3a;color:#3b8fc4;font-size:7px;text-align:center;line-height:21px;clip-path:polygon(0 25%,50% 0,100% 25%,100% 100%,0 100%)}

/* footer */
.site-footer{left:0;top:974px;width:693px;height:197px;background:var(--footer);border-top:2px solid #1c1c1c}
.footer-heading{height:19px;background:var(--blue-box);color:var(--white);font-size:9px;line-height:19px;text-align:center}
.footer-list{list-style:none;font-size:7px;color:var(--white)}
.footer-list li{height:18.7px;line-height:10px;padding-left:16px;position:relative}
.footer-list li::before{content:"";position:absolute;left:0;top:2px;border-left:6px solid var(--white);border-top:3px solid transparent;border-bottom:3px solid transparent}
.footer-text{font-size:7px;line-height:12.8px;color:var(--white);white-space:nowrap}
.footer-text .excerpt{color:var(--olive-light);border-bottom:1px solid var(--olive-light)}
.social{display:flex;gap:6px}
.social span{width:12px;height:12px;border-radius:50%}
.copyright{left:0;top:1171px;width:693px;height:29px;background:var(--bottom);color:var(--white);font-size:6.6px;text-align:center;line-height:29px}
</style>
</head>
<body>

<header class="abs site-header">
  <div class="abs brand"><span class="brand-small">PROPERTIES BY</span><span class="brand-name">VARDEN</span></div>
  <div class="abs user-links">Welcome Guest<span>|</span>Login<span>|</span>Register FREE</div>
  <nav class="abs main-nav">
    <a class="current" href="#">HOME</a><a href="#">COMMERCIAL</a><a href="#">RESIDENTIAL</a><a href="#">FORE</a><a href="#">RENT</a><a href="#">CONTACT</a>
  </nav>
</header>

<section class="abs hero" role="img" aria-label="Street view of a white low-rise commercial building with parked cars and pedestrians"></section>
<div class="abs hero-caption"></div>
<div class="abs hero-kicker">Lorem Ipsum</div>
<div class="abs hero-title">simply</div>
<div class="abs slide-arrow" style="left:59px;top:218px">&#10094;</div>
<div class="abs slide-arrow" style="left:617px;top:218px">&#10095;</div>

<form class="abs property-search" aria-label="Search for properties">
  <span class="tagline">Commercial and Residential Representation</span>
  <span class="search-field type">Property type &#9662;</span>
  <span class="search-field place">City or ZIP</span>
  <span class="search-button">SEARCH PROPERTIES</span>
</form>

<article class="abs card" style="left:59px">
  <div class="card-photo" role="img" aria-label="Large traditional house beside a lake" style="background:linear-gradient(180deg,#6c9fd6 0%,#a9c6e6 45%,#d9d8cf 62%,#6c8a3c 78%,#3f6173 100%)"></div>
  <div class="card-label">Commercial</div>
  <p class="card-text">Lorem Ipsum is simply dummy text of the printing and typesetting<br>Lorem Ipsum is simply dummy text of the printing and typesetting</p>
  <span class="read-more">Read more.....</span>
</article>
<article class="abs card" style="left:267px">
  <div class="card-photo" role="img" aria-label="Brick office building with a plaza sign" style="background:linear-gradient(180deg,#c9793e 0%,#a5562c 40%,#7a4a2c 70%,#3c3a2a 100%)"></div>
  <div class="card-label">Residential</div>
  <p class="card-text">Lorem Ipsum is simply dummy text of the printing and typesetting<br>Lorem Ipsum is simply dummy text of the printing and typesetting</p>
  <span class="read-more">Read more.....</span>
</article>
<article class="abs card" style="left:469px">
  <div class="card-photo" role="img" aria-label="Glass and brick office building" style="background:linear-gradient(135deg,#203a5c 0%,#4d6f95 40%,#9a7a66 70%,#5f7a4a 100%)"></div>
  <div class="card-label">Farm</div>
  <p class="card-text">Lorem Ipsum is simply dummy text of the printing and typesetting<br>Lorem Ipsum is simply dummy text of the printing and typesetting</p>
  <span class="read-more">Read more.....</span>
</article>
<div class="abs slide-arrow" style="left:54px;top:465px">&#10094;</div>
<div class="abs slide-arrow" style="left:623px;top:465px">&#10095;</div>

<div class="abs section-head" style="left:59px;top:638px"><h2 class="section-title">LATEST WORK</h2><span class="section-rule"></span></div>
<div class="abs feature-photo" role="img" aria-label="Two-storey brick office building" style="left:59px;top:675px;background:linear-gradient(180deg,#c8d6e3 0%,#dfe5ea 40%,#9a5a3c 55%,#7b4a33 72%,#6f6f6a 100%)"></div>
<p class="abs feature-text" style="left:216px;top:680px">Lorem Ipsum is simply dummy text of the printing and type-setting<br>&nbsp;Loremy text the printing and typesettingLoremy text<br>the printing and typesetting</p>
<span class="abs read-more" style="left:381px;top:739px">Read more...</span>

<div class="abs section-head" style="left:59px;top:812px"><h2 class="section-title">OUR SERVICES</h2><span class="section-rule"></span></div>
<div class="abs feature-photo" role="img" aria-label="Cheerful business team in an office" style="left:59px;top:849px;background:linear-gradient(135deg,#e8edf1 0%,#cfd6de 45%,#8d8f96 75%,#3c3d44 100%)"></div>
<p class="abs feature-text" style="left:216px;top:849px">Lorem Ipsum is simply dummy text of the printing and type-setting<br>&nbsp;Loremy text the printing and typesettingLoremy text<br>the printing and typesetting</p>
<span class="abs read-more" style="left:387px;top:922px">Read more...</span>

<aside class="abs discussions">
  <div class="discussions-head">LATEST DISCUSSIONS:</div>
  <div class="post" style="top:41px"><svg width="12" height="10" viewBox="0 0 12 10"><path d="M1 4a5 3.5 0 1 1 3 3.2L2 9.5l.4-2.8A4 3 0 0 1 1 4z" fill="#666"/></svg><span class="post-title">Lorem Ipsum is simply dummy</span><span class="post-meta">by : <b>Ipsum</b><span class="date">26-03-2014</span></span></div>
  <div class="post" style="top:77px"><svg width="12" height="10" viewBox="0 0 12 10"><path d="M1 4a5 3.5 0 1 1 3 3.2L2 9.5l.4-2.8A4 3 0 0 1 1 4z" fill="#666"/></svg><span class="post-title">Lorem Ipsum is simply dummy</span><span class="post-meta">by : <b>Ipsum</b><span class="date">26-03-2014</span></span></div>
  <div class="post" style="top:113px"><svg width="12" height="10" viewBox="0 0 12 10"><path d="M1 4a5 3.5 0 1 1 3 3.2L2 9.5l.4-2.8A4 3 0 0 1 1 4z" fill="#666"/></svg><span class="post-title">Lorem Ipsum is simply dummy</span><span class="post-meta">by : <b>Ipsum</b><span class="date">26-03-2014</span></span></div>
  <div class="post" style="top:149px"><svg width="12" height="10" viewBox="0 0 12 10"><path d="M1 4a5 3.5 0 1 1 3 3.2L2 9.5l.4-2.8A4 3 0 0 1 1 4z" fill="#666"/></svg><span class="post-title">Lorem Ipsum is simply dummy</span><span class="post-meta">by : <b>Ipsum</b><span class="date">26-03-2014</span></span></div>
  <div class="post" style="top:185px"><svg width="12" height="10" viewBox="0 0 12 10"><path d="M1 4a5 3.5 0 1 1 3 3.2L2 9.5l.4-2.8A4 3 0 0 1 1 4z" fill="#666"/></svg><span class="post-title">Lorem Ipsum is simply dummy</span><span class="post-meta">by : <b>Ipsum</b><span class="date">26-03-2014</span></span></div>
  <div class="post" style="top:221px"><svg width="12" height="10" viewBox="0 0 12 10"><path d="M1 4a5 3.5 0 1 1 3 3.2L2 9.5l.4-2.8A4 3 0 0 1 1 4z" fill="#666"/></svg><span class="post-title">Lorem Ipsum is simply dummy</span><span class="post-meta">by : <b>Ipsum</b><span class="date">26-03-2014</span></span></div>
  <div class="view-all">VIEW ALL POSTS</div>
</aside>

<footer class="abs site-footer">
  <div class="abs footer-heading" style="left:59px;top:41px;width:71px">Quick link</div>
  <ul class="abs footer-list" style="left:59px;top:78px">
    <li>Home</li><li>Commercial</li><li>Residential</li><li>Fore</li><li>Rent</li><li>Contact</li>
  </ul>

  <div class="abs footer-heading" style="left:203px;top:41px;width:69px">About Us</div>
  <ul class="abs footer-list" style="left:203px;top:78px">
    <li>Lorem Ipsum</li><li>Lorem Ipsum</li><li>Lorem Ipsum</li><li>Lorem Ipsum</li><li>Lorem Ipsum</li><li>Lorem Ipsum</li>
  </ul>

  <div class="abs footer-heading" style="left:336px;top:41px;width:60px">Blog</div>
  <p class="abs footer-text" style="left:335px;top:74px">Lorem Ipsum is simply dummy text<br>of the printing and typesetting<br><span class="excerpt">industry's standard industry's stan-</span></p>
  <p class="abs footer-text" style="left:335px;top:133px">Lorem Ipsum is simply dummy text<br>of the printing and typesetting<br><span class="excerpt">industry's standard dard</span></p>

  <div class="abs footer-heading" style="left:514px;top:42px;width:70px">Contact Us</div>
  <p class="abs footer-text" style="left:514px;top:74px">Lorem Ipsum is simply dummy text<br>of the printing and typesetting<br>of the printing and typesetting</p>
  <div class="abs footer-text" style="left:514px;top:118px">
    <svg width="6" height="9" viewBox="0 0 6 9" style="vertical-align:-1px"><path d="M1 0h2l-.5 2.5-1 .5c.3 1.3 1 2.4 2 3l.8-.6L6 7.2 5 9C2 8.4 0 5 0 1.5z" fill="#fff"/></svg>
    &nbsp;&nbsp;: +1-0530-555-0142</div>
  <div class="abs footer-text" style="left:514px;top:135px">
    <svg width="11" height="8" viewBox="0 0 11 8" style="vertical-align:-1px"><rect x=".5" y=".5" width="10" height="7" fill="none" stroke="#fff"/><path d="M.5.5l5 4 5-4" fill="none" stroke="#fff"/></svg>
    :&nbsp;&nbsp;mail.tlvarden.com</div>
  <div class="abs social" style="left:514px;top:163px" aria-label="Social links">
    <span style="background:#3b5a9a"></span><span style="background:#2aa3d8"></span><span style="background:#1a7bb4"></span><span style="background:#d6473a"></span>
  </div>
</footer>
<div class="abs copyright">Copyright © 2014 . All rights reserved.</div>

</body>
</html>
```